we can communicate on this, but i want to follow the approach we took on Pellew|Marsh & Quinlan but i feel the card front needs the black background and the platinum and gold logo. The back? I am open. we can use the same info from PM&Q. Velmont Arc is an enhanced equity investment fund - basically a very exclusive boutique hedge fund that uses only stock options. very advanced things. hope you are interested

Contact Information for Business Card

Dr. Lewis T. Brennick, CFA
Scientifique de fusée financière
701.555.0143
LTBquant47@mailvantor.com

4718 Willow Creek Bend W.
West Fargo, ND 58078

No web site

Colors

Designer to choose colors to be used in the design.

Requirements
Nice to have
• I tend to prefer the most visible applications of the logo to include logo and name, the logo version with a black background and the gold and platinum components separated by the black. I see this working well for a single side (logo and name - this is card front to me).
• I am fairly open to other treatments on the reverse side with the data. To me, it makes sense to have a different color rendition of the logo on the reverse and it may be a muted black tone on tone or an oversized portion that would have spot UV. Or, the reverse may play with colors and layout
Should not have
• Other colors = no no
• Decorative font

```html
<!DOCTYPE html>
<html lang="en">
<head>
<meta charset="utf-8">
<title>Velmont Arc – Business Card</title>
<link rel="stylesheet" href="https://fonts.googleapis.com/css2?family=Montserrat:wght@600&family=Open+Sans:wght@400;600&display=swap">
<style>
  :root {
    --backdrop: #e8e5e0;
    --card-black: #1c1c1c;
    --gold: #d4a72c;
    --gold-deep: #b88a1c;
    --text-white: #f4f4f4;
    --divider: #cfcfcf;
  }
  * { margin: 0; padding: 0; box-sizing: border-box; }
  html, body {
    width: 1200px; height: 1000px; overflow: hidden;
    background: var(--backdrop);
  }
  .canvas { position: relative; width: 1200px; height: 1000px; }
  .card {
    position: absolute;
    width: 666px; height: 396px;
    border-radius: 22px;
    background: var(--card-black);
    box-shadow: 0 4px 14px rgba(0,0,0,0.25);
  }
  .card--front { left: 262px; top: 75px; }
  .card--back  { left: 267px; top: 535px; }

  .brand {
    position: absolute; left: 38px; width: 280px; top: 92px;
    display: flex; flex-direction: column; align-items: center;
  }
  .brand__dot {
    width: 120px; height: 120px; border-radius: 50%;
    background: linear-gradient(135deg, var(--gold) 0%, var(--gold-deep) 100%);
  }
  .brand__name {
    margin-top: 36px;
    font-family: 'Montserrat', sans-serif; font-weight: 600;
    font-size: 36px; letter-spacing: 1px; color: var(--text-white);
    white-space: nowrap;
  }

  .divider {
    position: absolute; left: 337px; top: 97px;
    width: 2px; height: 203px; background: var(--divider);
  }

  .details {
    position: absolute; left: 370px; top: 96px; width: 280px;
    font-family: 'Open Sans', sans-serif; color: var(--text-white);
    font-size: 17px; line-height: 22px;
  }
  .details__name {
    color: var(--gold); font-weight: 600; font-size: 17px;
    text-transform: uppercase; white-space: nowrap;
  }
  .details__title { margin-bottom: 10px; white-space: nowrap; }
  .details__address { margin-bottom: 8px; white-space: nowrap; }
  .contact-list { list-style: none; }
  .contact-list li {
    display: flex; align-items: center; height: 24.5px; white-space: nowrap;
  }
  .contact-list svg { width: 15px; height: 13px; margin-right: 7px; fill: var(--gold); flex: none; }

  .back-mark {
    position: absolute; inset: 0;
    display: flex; flex-direction: column; align-items: center; justify-content: center;
  }
  .back-mark__dot {
    width: 200px; height: 200px; border-radius: 50%;
    background: linear-gradient(135deg, var(--gold) 0%, var(--gold-deep) 100%);
  }
  .back-mark__name {
    margin-top: 26px;
    font-family: 'Montserrat', sans-serif; font-weight: 600;
    font-size: 30px; letter-spacing: 1px; color: var(--text-white);
  }
</style>
</head>
<body>
<div class="canvas">

  <section class="card card--front">
    <div class="brand">
      <div class="brand__dot"></div>
      <div class="brand__name">VELMONT ARC</div>
    </div>

    <div class="divider"></div>

    <div class="details">
      <p class="details__name">Dr. Lewis T. Brennick, CFA</p>
      <p class="details__title">Scientifique de fusée financière</p>
      <p class="details__address">4718 Willow Creek Bend W.<br>West Fargo, ND 58078</p>
      <ul class="contact-list">
        <li><svg viewBox="0 0 16 14"><path d="M1 5 C1 2 4 1 8 1 C12 1 15 2 15 5 L12 5 L11 3 L5 3 L4 5 Z M3 6 H13 L14 13 H2 Z"/></svg>701.555.0143</li>
        <li><svg viewBox="0 0 16 14"><path d="M1 2 H15 V12 H1 Z M1 2 L8 8 L15 2"/></svg>LTBquant47@mailvantor.com</li>
      </ul>
    </div>
  </section>

  <section class="card card--back">
    <div class="back-mark">
      <div class="back-mark__dot"></div>
      <div class="back-mark__name">VELMONT ARC</div>
    </div>
  </section>

</div>
</body>
</html>
```